Business Card Design For Office Furniture Clearance Company

Kestrel Office Clearance - our company name pretty much explains what we do, we clear offices for high end clients, mainly plc's and large international companies.

We require a nice looking business card that displays professionalism but without being too serious.

It would be nice to see just a little more than a conventional boring business card, make sure you add some flare.

Industry/Entity Type

Office Furniture

Contact Information for Business Card

CARD 1

Mark Holloway
Director
mark@kestrelofficeclearance.co.uk
m: 07700 153928

t: 01632 960418
www.kestrelofficeclearance.co.uk

Kestrel Office Clearance
Unit K4 B
2-8 Fenwick Lane
Ashcombe
Wendlebury
ZZ9 4QT

free office clearances… you cant get better than that.

CARD 2

Peter Radford
Director
peter@kestrelofficeclearance.co.uk
m: 07700 382615

t: 01632 960418

Kestrel Office Clearance
Unit K4 B
2-8 Fenwick Lane
Ashcombe
Wendlebury
ZZ9 4QT

Font styles to use
Sans Serif

Requirements
Must have
• A white background - as we have a blue logo.
Nice to have
• Nice use of the logo - play around with this and dissect it.

```html
<!DOCTYPE html>
<html lang="en">
<head>
<meta charset="utf-8">
<title>Kestrel Office Clearance – Business Card</title>
<link rel="stylesheet" href="https://fonts.googleapis.com/css2?family=Source+Sans+3:ital,wght@0,400;0,600;1,400&display=swap">
<style>
  :root {
    --page: #9b9c9c;
    --brand-blue: #0b69a8;
    --paper: #e3e4e8;
    --text-light: #eef2f6;
    --charcoal: #3b3b3d;
    --ink-dark: #3b3b3d;
    --tagline: #d6d6d8;
  }
  * { margin: 0; padding: 0; box-sizing: border-box; }
  html, body {
    width: 1105px;
    height: 1200px;
    overflow: hidden;
    background: var(--page);
    font-family: "Source Sans 3", "Helvetica Neue", Arial, sans-serif;
  }
  .card {
    position: absolute;
    left: 182px;
    width: 746px;
    height: 427px;
    overflow: hidden;
  }
  .card--front { top: 119px; }
  .card--back { top: 637px; }
  .card__art {
    position: absolute;
    inset: 0;
    width: 100%;
    height: 100%;
  }
  .contact-block {
    position: absolute;
    left: 37px;
    color: var(--text-light);
  }
  .person { top: 38px; }
  .person__name {
    font-size: 27px;
    font-weight: 600;
    letter-spacing: 0.5px;
    line-height: 1;
    text-transform: uppercase;
  }
  .person__role {
    font-size: 19px;
    line-height: 1;
    margin-top: 6px;
    text-transform: uppercase;
  }
  .address {
    top: 160px;
    font-size: 20px;
    line-height: 26px;
    font-style: normal;
  }
  .address__company { font-weight: 600; }
  .contacts {
    top: 278px;
    list-style: none;
    font-size: 20px;
    line-height: 28.5px;
  }
  .contacts li {
    display: flex;
    align-items: center;
    gap: 9px;
  }
  .contacts svg {
    width: 17px;
    height: 17px;
    fill: var(--text-light);
    flex: none;
  }
  .brand-mark {
    position: absolute;
    display: flex;
    align-items: center;
    justify-content: center;
    border-radius: 50%;
  }
  .brand-mark--front {
    left: 424px;
    top: 93px;
    width: 240px;
    height: 240px;
  }
  .brand-mark--back {
    left: 258px;
    top: 81px;
    width: 230px;
    height: 230px;
  }
  .brand-name {
    font-weight: 600;
    font-size: 26px;
    line-height: 1;
    letter-spacing: 1px;
    text-transform: uppercase;
  }
  .brand-mark--front .brand-name { color: var(--text-light); }
  .brand-mark--back .brand-name { color: var(--ink-dark); }
  .tagline {
    position: absolute;
    left: 0;
    right: 0;
    top: 345px;
    text-align: center;
    font-style: italic;
    font-size: 20px;
    color: var(--tagline);
  }
</style>
</head>
<body>

<section class="card card--front" aria-label="Business card front">
  <svg class="card__art" viewBox="0 0 540 309" preserveAspectRatio="none" aria-hidden="true">
    <rect width="540" height="309" fill="var(--brand-blue)"/>
    <path d="M335 0 C 205 45, 190 250, 373 309 L 540 309 L 540 0 Z" fill="var(--paper)"/>
    <circle cx="394" cy="154" r="87" fill="var(--brand-blue)"/>
  </svg>

  <div class="brand-mark brand-mark--front"><span class="brand-name">Kestrel</span></div>

  <div class="contact-block person">
    <p class="person__name">Mark Holloway</p>
    <p class="person__role">Director</p>
  </div>

  <address class="contact-block address">
    <span class="address__company">Kestrel Office Clearance</span><br>
    Unit K4 B, 2-8 Fenwick Lane<br>
    Ashcombe, Wendlebury<br>
    ZZ9 4QT
  </address>

  <ul class="contact-block contacts">
    <li>
      <svg viewBox="0 0 24 24" aria-hidden="true"><path d="M6.6 10.8a15.1 15.1 0 0 0 6.6 6.6l2.2-2.2c.3-.3.7-.4 1-.2 1.1.4 2.3.6 3.6.6.6 0 1 .4 1 1V20c0 .6-.4 1-1 1A17 17 0 0 1 3 4c0-.6.4-1 1-1h3.5c.6 0 1 .4 1 1 0 1.3.2 2.5.6 3.6.1.3 0 .7-.2 1z"/></svg>
      <span>01632 960418</span>
    </li>
    <li>
      <svg viewBox="0 0 24 24" aria-hidden="true"><path d="M7 1h10a2 2 0 0 1 2 2v18a2 2 0 0 1-2 2H7a2 2 0 0 1-2-2V3a2 2 0 0 1 2-2zm0 3v14h10V4zm5 15.2a1.1 1.1 0 1 0 0 2.2 1.1 1.1 0 0 0 0-2.2z"/></svg>
      <span>07700 153928</span>
    </li>
    <li>
      <svg viewBox="0 0 24 24" aria-hidden="true"><path d="M2 5h20v14H2zm2 2v.4l8 5.2 8-5.2V7zm0 2.8V17h16V9.8l-8 5.2z"/></svg>
      <span>mark@kestrelofficeclearance.co.uk</span>
    </li>
    <li>
      <svg viewBox="0 0 24 24" aria-hidden="true"><path d="M12 2a10 10 0 1 0 0 20 10 10 0 0 0 0-20zm-1 17.9A8 8 0 0 1 4.1 10L9 15v1a2 2 0 0 0 2 2zm6.9-2.5A2 2 0 0 0 16 16h-1v-3a1 1 0 0 0-1-1H8v-2h2a1 1 0 0 0 1-1V7h2a2 2 0 0 0 2-2v-.4a8 8 0 0 1 2.9 12.8z"/></svg>
      <span>www.kestrelofficeclearance.co.uk</span>
    </li>
  </ul>
</section>

<section class="card card--back" aria-label="Business card back">
  <svg class="card__art" viewBox="0 0 540 309" preserveAspectRatio="none" aria-hidden="true">
    <rect width="540" height="309" fill="var(--charcoal)"/>
    <circle cx="270" cy="142" r="83" fill="var(--paper)"/>
  </svg>
  <div class="brand-mark brand-mark--back"><span class="brand-name">Kestrel</span></div>
  <p class="tagline">Free office clearances… you cant get better than that.</p>
</section>

</body>
</html>
```